OBK Farcoast Logistics Limited

We need the buissnes card to be very exclusive. As we are all young in our company. We need this to be the gate to make our clients feel deep interest for us.

We are focused in as International Trade advisors, and our products go from Oil Tanker Ships to Rubber balls for dogs.

Our Slogan is Bringing Far Close.
And our main marketing will be through Internet.

We were stablished in 2009 In Mexico and we also have offices in Hong Kong.
We have representatives in China and Europe.

Target Market(s)

Is every company or Individual that wants to develop an International Project or product development or Logistic service of Goods and people.
Some of our current projects are Ship Brokerage, Mine Brokerage, Real State and Product Pormotional development.

Industry/Entity Type

It Company

Requirements
Must have
• Our Logo and slogan, and make the card accoriding to the logo.
Nice to have
• Our Colors

```html
<!DOCTYPE html>
<html lang="en">
<head>
<meta charset="utf-8">
<title>OBK Farcoast Logistics Limited – Business Card Concepts</title>
<link rel="stylesheet" href="https://fonts.googleapis.com/css2?family=Exo:wght@400;800&family=Open+Sans:wght@400&display=swap">
<style>
  :root {
    --backdrop: #e9e6e1;
    --white: #ffffff;
    --brand-blue: #1a7db4;
    --brand-sky: #29a3dc;
    --brand-green: #8cc63f;
    --card-black: #262626;
    --ink: #2b2b2b;
    --shadow: rgba(0, 0, 0, 0.25);
  }
  * { box-sizing: border-box; margin: 0; padding: 0; }
  html, body {
    width: 1200px;
    height: 490px;
    overflow: hidden;
    background: var(--backdrop);
  }
  .sheet {
    position: relative;
    width: 1200px;
    height: 490px;
  }
  .card {
    position: absolute;
    width: 375px;
    height: 214px;
    display: flex;
    flex-direction: column;
    align-items: center;
    box-shadow: 0 2px 6px var(--shadow);
  }
  .card--front-white { left: 90px;  top: 16px;  background: var(--white); }
  .card--back-white  { left: 492px; top: 16px;  background: var(--white); }
  .card--blue        { left: 18px;  top: 257px; background: var(--brand-blue); }
  .card--green       { left: 415px; top: 257px; background: var(--brand-green); }
  .card--black       { left: 812px; top: 259px; background: var(--card-black); }

  /* mark area: plain circle beside the company name */
  .mark {
    margin-top: 50px;
    height: 90px;
    display: flex;
    align-items: center;
    gap: 12px;
  }
  .mark__dot {
    width: 40px;
    height: 40px;
    border-radius: 50%;
    background: var(--brand-sky);
  }
  .mark__name {
    font-family: "Exo", sans-serif;
    font-weight: 800;
    font-size: 52px;
    letter-spacing: 3px;
    color: var(--brand-sky);
  }

  /* wordmark + slogan */
  .name {
    margin-top: 54px;
    font-family: "Exo", sans-serif;
    font-weight: 800;
    font-size: 88px;
    line-height: 66px;
    letter-spacing: 10px;
    padding-left: 10px;
  }
  .slogan {
    margin-top: 6px;
    font-family: "Exo", sans-serif;
    font-weight: 400;
    font-size: 20px;
    line-height: 22px;
  }
  .card--back-white .name { color: var(--brand-green); }
  .card--back-white .slogan { color: var(--brand-sky); }
  .card--blue .name, .card--blue .slogan,
  .card--green .name, .card--green .slogan { color: var(--white); }

  .details {
    margin-top: auto;
    margin-bottom: 12px;
    font-family: "Open Sans", sans-serif;
    font-size: 10.5px;
    line-height: 16px;
    text-align: center;
    color: var(--ink);
  }
  .card--blue .details, .card--green .details, .card--black .details { color: var(--white); }
  .details__sep { color: var(--brand-sky); padding: 0 3px; }
  .card--black .details__sep { color: var(--brand-green); }
  .card--black .mark__dot { background: var(--brand-blue); }
</style>
</head>
<body>
<main class="sheet">

  <section class="card card--front-white">
    <div class="mark">
      <span class="mark__dot"></span>
      <span class="mark__name">OBK</span>
    </div>
    <p class="details">Offices : Lima &amp; Singapore<br>Representative Agents in Korea &amp; Africa</p>
  </section>

  <section class="card card--back-white">
    <h1 class="name">OBK</h1>
    <p class="slogan">Bringing Far Close</p>
    <p class="details">Offices : Lima <span class="details__sep">•</span> Singapore<br>Representative Agents: Korea &amp; Africa</p>
  </section>

  <section class="card card--blue">
    <h2 class="name">OBK</h2>
    <p class="slogan">Bringing Far Close</p>
    <p class="details">Offices : Lima &amp; Singapore<br>Representative Agents in Korea &amp; Africa</p>
  </section>

  <section class="card card--green">
    <h2 class="name">OBK</h2>
    <p class="slogan">Bringing Far Close</p>
    <p class="details">Offices : Lima &amp; Singapore<br>Representative Agents in Korea &amp; Africa</p>
  </section>

  <section class="card card--black">
    <div class="mark">
      <span class="mark__dot"></span>
      <span class="mark__name">OBK</span>
    </div>
    <p class="details">Offices : Lima <span class="details__sep">•</span> Singapore<br>Representative Agents: Korea &amp; Africa</p>
  </section>

</main>
</body>
</html>
```